Create modern and sleek business card for luxury real estate company

We're a "boutique" real estate office looking for a design that gets across a highly modern luxury brand. Blacks and whites are probably the best colors unless we try a silver foil for the logo. I've attached a version of our current logo here. I'd like to swap out the current font on there with Gotham Light Regular.

I'm looking to have one side of the card have the logo with the space for our agents info on the other side.

Target Market(s)

Young professionals in a "luxury" headspace

Industry/Entity Type

Real estate

Contact Information for Business Card

A place for agent name, cell number, website. The slogan "Simply Rethinking Real Estate".

Font styles to use
Other font styles liked:
• Gotham Regular

Colors

Designer to choose only greyscale colors for use in the design.

Requirements
Must have
• Matte black as the background color. Clean lines and use of contrast. A specific design aspect that will use silver foil.
Nice to have
• Up in the air on integrating a QR code
Should not have
• Any houses or other real estate related design (ex: a clip art house)

```html
<!DOCTYPE html>
<html lang="en">
<head>
<meta charset="utf-8">
<title>Halden Realty — Business Card</title>
<link href="https://fonts.googleapis.com/css2?family=Tinos:wght@400;700&family=Arimo:wght@400&display=swap" rel="stylesheet">
<style>
  :root {
    --page: #3a3a3a;
    --card-black: #141414;
    --card-black-soft: #1d1d1d;
    --silver-light: #e8e8e8;
    --silver-mid: #a9a9a9;
    --silver-dark: #5c5c5c;
    --ink: #f2f2f2;
    --ink-soft: #bdbdbd;
    --divider: #3a3a3a;
  }
  * { margin: 0; padding: 0; box-sizing: border-box; }
  html, body {
    width: 1200px; height: 1015px; overflow: hidden;
    background: var(--page);
  }
  .canvas {
    position: relative; width: 1200px; height: 1015px;
    display: flex; flex-direction: column; align-items: center; justify-content: center;
    gap: 60px;
  }
  .card {
    position: relative; width: 740px; height: 422px;
    background: linear-gradient(135deg, var(--card-black-soft), var(--card-black));
    box-shadow: 0 14px 30px rgba(0,0,0,0.55);
    overflow: hidden;
  }
  /* Back side: foil pattern field */
  .foil-field {
    position: absolute; inset: 0;
    background: linear-gradient(120deg, var(--card-black) 0%, #262626 45%, var(--card-black) 100%);
  }
  .back-mark {
    position: absolute; left: 500px; top: 194px;
    display: flex; align-items: center; gap: 12px;
  }
  .mark-circle {
    width: 34px; height: 34px; border-radius: 50%;
    border: 3px solid var(--silver-light);
    flex: none;
  }
  .back-mark .brand-name {
    font-family: "Tinos", serif; font-weight: 400; font-size: 20px;
    letter-spacing: 2px; color: var(--silver-light); white-space: nowrap;
  }
  /* Front side */
  .brand-block {
    position: absolute; left: 0; top: 0; width: 370px; height: 100%;
    display: flex; flex-direction: column; align-items: center; justify-content: center; gap: 16px;
  }
  .brand-block .mark-circle { width: 86px; height: 86px; border-width: 4px; }
  .brand-block .brand-name {
    font-family: "Tinos", serif; font-weight: 400; font-size: 40px;
    letter-spacing: 3px; color: var(--silver-light); text-align: center; line-height: 1.15;
  }
  .slogan {
    font-family: "Arimo", sans-serif; font-size: 13px; letter-spacing: 2px;
    text-transform: uppercase; color: var(--silver-mid); white-space: nowrap;
  }
  .info-block {
    position: absolute; left: 370px; top: 0; width: 370px; height: 100%;
    border-left: 1px solid var(--divider);
    padding: 92px 0 0 40px;
    color: var(--ink);
  }
  .agent-name {
    font-family: "Tinos", serif; font-weight: 700; font-size: 24px; letter-spacing: 1px;
  }
  .agent-title {
    font-family: "Arimo", sans-serif; font-size: 16px; color: var(--ink-soft); margin-bottom: 16px;
  }
  .contact-list { list-style: none; font-family: "Arimo", sans-serif; font-size: 17px; }
  .contact-list li { display: flex; align-items: center; gap: 8px; line-height: 26px; }
  .contact-list svg { width: 15px; height: 15px; flex: none; }
  .address {
    font-family: "Arimo", sans-serif; font-size: 17px; line-height: 24px; margin-top: 18px;
  }
</style>
</head>
<body>
<main class="canvas">
  <section class="card card-back">
    <div class="foil-field" role="img" aria-label="Silver foil repeating brand pattern across the card"></div>
    <div class="back-mark">
      <span class="mark-circle"></span>
      <span class="brand-name">HALDEN REALTY</span>
    </div>
  </section>

  <section class="card card-front">
    <div class="brand-block">
      <span class="mark-circle"></span>
      <span class="brand-name">HALDEN<br>REALTY</span>
      <span class="slogan">Simply Rethinking Real Estate</span>
    </div>
    <div class="info-block">
      <h1 class="agent-name">MARCUS HALE</h1>
      <p class="agent-title">Managing Director</p>
      <ul class="contact-list">
        <li>
          <svg viewBox="0 0 16 16" aria-hidden="true"><path d="M4 1.5 6.5 4 5 6c.8 1.8 2.2 3.2 4 4l2-1.5 2.5 2.5-1.5 2.5C7 13 3 9 1.5 3z" fill="var(--ink)"/></svg>
          055-210 678 431
        </li>
        <li>
          <svg viewBox="0 0 16 16" aria-hidden="true"><rect x="1" y="3.5" width="14" height="9" fill="var(--ink)"/><path d="M1 3.5 8 9l7-5.5" stroke="var(--card-black)" stroke-width="1.2" fill="none"/></svg>
          hello@haldenrealty.com
        </li>
        <li>
          <svg viewBox="0 0 16 16" aria-hidden="true"><g fill="none" stroke="var(--ink)" stroke-width="1.4"><circle cx="8" cy="8" r="6.5"/><ellipse cx="8" cy="8" rx="2.8" ry="6.5"/><path d="M1.5 8h13"/></g></svg>
          www.haldenrealty.com
        </li>
      </ul>
      <p class="address">18, Linden Court Avenue<br>60217, Northland</p>
    </div>
  </section>
</main>
</body>
</html>
```